We need a Welcome Booklet designed for our Church - Harrowgate Fields Church. We would like a design that is contemporary with no religious symbols or old pictures. Please use quality contemporary photos . See attached a Word document with what content we want in the booklet.

Target Market(s)

Guests to the church so new person friendly

Requirements
Must have
• A contemporary modern look
Should not have
• Religious symbols or old pictures

```html
<!DOCTYPE html>
<html lang="en">
<head>
<meta charset="utf-8">
<title>Discipleship at HFC</title>
<link href="https://fonts.googleapis.com/css2?family=Bitter:wght@400&family=Questrial&family=Montserrat:ital,wght@0,700;1,700&display=swap" rel="stylesheet">
<style>
  :root {
    --page: #ffffff;
    --ink: #1b1b1b;
    --band: #000000;
    --white: #ffffff;
    --accent-blue: #2f86f0;
    --badge-green: #86e11c;
    --header-dark: #16230f;
    --header-mid: #3c5a22;
    --photo-warm: #c9a77e;
    --photo-cool: #6b86a8;
    --social-one: #55c8ee;
    --social-two: #2c5fd4;
    --social-three: #d2362b;
  }
  * { box-sizing: border-box; margin: 0; padding: 0; }
  html, body { width: 855px; height: 1200px; overflow: hidden; background: var(--page); }
  .page { position: relative; width: 855px; height: 1200px; overflow: hidden; background: var(--page); color: var(--ink); font-family: "Questrial", "Century Gothic", sans-serif; }

  .hero { position: absolute; left: 0; top: 0; width: 855px; height: 200px;
    background: radial-gradient(ellipse at 70% 40%, var(--header-mid) 0%, var(--header-dark) 70%),
                linear-gradient(90deg, var(--header-mid), var(--header-dark)); }
  .hero-title { position: absolute; left: 54px; top: 108px; font-family: "Bitter", Georgia, serif; font-weight: 400; font-size: 48px; line-height: 1; color: var(--white); letter-spacing: -0.3px; }

  .copy { position: absolute; left: 54px; width: 720px; font-size: 22px; line-height: 28.5px; color: var(--ink); }
  .intro { top: 240px; }
  .connect-heading { position: absolute; left: 54px; top: 336px; font-family: "Montserrat", Arial, sans-serif; font-style: italic; font-weight: 700; font-size: 22px; color: var(--accent-blue); }
  .connect { top: 364px; }
  .contact-note { top: 500px; }

  .contact-band { position: absolute; left: 0; top: 647px; width: 855px; height: 150px; background: var(--band); color: var(--white); }
  .contact-item { position: absolute; display: flex; align-items: center; font-size: 24px; }
  .contact-item svg { position: absolute; left: 0; }
  .contact-item span { position: absolute; white-space: nowrap; }
  .item-phone { left: 72px; top: 38px; }
  .item-email { left: 72px; top: 108px; }
  .item-card { left: 470px; top: 38px; }
  .item-web  { left: 470px; top: 108px; }
  .item-phone span, .item-email span { left: 67px; }
  .item-card span, .item-web span { left: 55px; }

  .social-badge { position: absolute; left: 651px; top: 771px; width: 172px; height: 172px; border-radius: 50%; background: var(--badge-green); border: 6px solid var(--white); display: flex; align-items: center; justify-content: center; text-align: center; font-family: "Montserrat", Arial, sans-serif; font-weight: 700; font-size: 24px; line-height: 33px; color: var(--white); }

  .community-photo { position: absolute; left: 58px; top: 838px; width: 404px; height: 297px;
    background: radial-gradient(circle at 55% 50%, var(--photo-warm) 0%, #a9837a 35%, var(--photo-cool) 75%, #3c4f7a 100%); }

  .social-list { position: absolute; left: 505px; top: 838px; }
  .social-entry { position: absolute; left: 0; font-size: 20px; white-space: nowrap; color: var(--ink); }
  .social-entry .tile { display: block; width: 66px; height: 66px; margin-bottom: 8px; }
  .entry-one { top: 0; }
  .entry-one .tile { background: var(--social-one); }
  .entry-two { top: 102px; }
  .entry-two .tile { background: var(--social-two); }
  .entry-three { top: 211px; }
  .entry-three .tile { background: var(--social-three); }
</style>
</head>
<body>
<main class="page">
  <header class="hero" role="img" aria-label="Photo of a congregation seated together, tinted dark green">
    <h1 class="hero-title">Discipleship at HFC</h1>
  </header>

  <p class="copy intro">We need relationships to grow and we would love to stay in touch with you.</p>

  <h2 class="connect-heading">Get connected</h2>
  <p class="copy connect">We need relationships to grow and we would love you stay in touch with you. Please fill out our connect card.&nbsp; HFC complies with the General Data Protection Regulation (GDPR).</p>

  <p class="copy contact-note">Additionally, there are a number of ways that you can contact us. Please let us know how you found your first time at HFC; we would love to hear from you and are looking forward to getting to know you.</p>

  <section class="contact-band">
    <div class="contact-item item-phone">
      <svg width="42" height="32" viewBox="0 0 42 32" style="top:-16px" aria-hidden="true">
        <path d="M2 10 C2 2 40 2 40 10 L40 14 L30 14 L30 9 L12 9 L12 14 L2 14 Z" fill="#fff"/>
        <path d="M10 14 L32 14 L38 30 L4 30 Z" fill="#fff"/>
        <circle cx="21" cy="22" r="4.5" fill="#000"/>
      </svg>
      <span style="top:-14px">Call us on 0121 4960731</span>
    </div>
    <div class="contact-item item-email">
      <svg width="44" height="30" viewBox="0 0 44 30" style="top:-15px" aria-hidden="true">
        <rect x="1" y="1" width="42" height="28" fill="#fff"/>
        <path d="M1 1 L22 17 L43 1" fill="none" stroke="#000" stroke-width="3"/>
        <path d="M1 29 L17 13 M43 29 L27 13" stroke="#000" stroke-width="3"/>
      </svg>
      <span style="top:-14px">Email us @ admin@hfc.life</span>
    </div>
    <div class="contact-item item-card">
      <svg width="38" height="38" viewBox="0 0 38 38" style="top:-19px" aria-hidden="true">
        <rect x="2" y="2" width="26" height="34" fill="none" stroke="#fff" stroke-width="3"/>
        <path d="M7 10 H23 M7 15 H23 M7 20 H23 M7 25 H23 M7 30 H18" stroke="#fff" stroke-width="2.5"/>
        <path d="M26 30 L35 17 L38 19 L29 32 L25 34 Z" fill="#fff"/>
      </svg>
      <span style="top:-14px">Fill in a Connect Card</span>
    </div>
    <div class="contact-item item-web">
      <svg width="42" height="32" viewBox="0 0 42 32" style="top:-16px" aria-hidden="true">
        <rect x="5" y="2" width="32" height="22" fill="none" stroke="#fff" stroke-width="3"/>
        <path d="M11 9 H31" stroke="#fff" stroke-width="2"/>
        <path d="M1 27 H41 V30 H1 Z" fill="#fff"/>
      </svg>
      <span style="top:-14px">Website: hfc.life</span>
    </div>
  </section>

  <div class="social-badge">Or find<br>us on<br>Social<br>Media</div>

  <div class="community-photo" role="img" aria-label="Photo from above of a diverse group joining hands in a circle"></div>

  <div class="social-list">
    <div class="social-entry entry-one"><span class="tile"></span>@ hfc_tweets</div>
    <div class="social-entry entry-two"><span class="tile"></span>@ Harrowgate Fields Church</div>
    <div class="social-entry entry-three"><span class="tile"></span>@ Harrowgate Fields Church</div>
  </div>
</main>
</body>
</html>
```